Stylish but eye catching vehicle signage for a Building and Carpentry business based in Sydney.**

We need vehicle signage for our White 2013 VW Transporter Van. We are not looking for a full wrap just signage that is eye catching, and memorable. Although we are a construction business our branding and Logo is sophisticated and clean and had a modern design . We would like to have vehicle branding that is consistent with that .

Our Logo is in grey and we would like to keep the design eye catching without using bright colours, we are not opposed to colour , we have used greys and ocre (brownish yellow)is our branding and would consider designs using these colours.

We would like to see designs that are stylish and sophisticated and not ones featuring tools or equipment for construction . We would like to see designs that portray our skills in the field of design .

Below I will attach our full logo and some examples of vehicle signage we like.
We would like the logo and contact details (email address and mobile number) on the sides and back.
We would also like the description
' new builds I renovations I residential I commercial '
at the bottom of the sides of the car between the wheels.
Updates

Hi Designers The contact details we would like on the vehicle are: 0471 839 204 rbexleybuilds@maplorn.com Just those two. Thanks

Target Market(s)

We would like to attract clients that are looking for quality work done right and professionally , and are happy to pay for good quality.

Contact Information for Business Card

I would like to go for a business card design that will accomodate embossing .
I would like the full logo on the front of the business card , no contact infomation.
The house or building icon in our logo will be raised or embossed by the printing company, so the back or the card will show the icon debossed (indented) .
On the back of the business card I would like the contact person's details:
DORIAN WEBB
carpenter
project manager
....and also the email address and mobile number on the back too.

Font styles to use
Sans Serif
Other font styles liked:
• Futura Lt Bt

Colors

Designer to choose only greyscale colors for use in the design.

Requirements
Must have
• Our logo (big and clear) and mobile number and email address on both sides and the back
Nice to have
• Designs or patterns that look architectural and elegant.
Should not have
• Any construction tools or equipment .
Designs like flames or lightning bolts
Too much colour or very bright colours

```html
<!DOCTYPE html>
<html lang="en">
<head>
<meta charset="utf-8">
<title>Bexley Builds — Business Cards</title>
<link rel="stylesheet" href="https://fonts.googleapis.com/css2?family=Jost:wght@300;400&display=swap">
<style>
  :root {
    --backdrop: #e4e4e4;
    --card: #6a6a6a;
    --ink: #ffffff;
  }
  * { margin: 0; padding: 0; box-sizing: border-box; }
  html, body {
    width: 1200px;
    height: 1200px;
    overflow: hidden;
    background: var(--backdrop);
    font-family: "Jost", "Futura", sans-serif;
    color: var(--ink);
  }
  .canvas { position: relative; width: 1200px; height: 1200px; }
  .card {
    position: absolute;
    left: 412px;
    width: 388px;
    height: 225px;
    background: var(--card);
  }
  .card--front-a { top: 45px; }
  .card--back-a  { top: 335px; }
  .card--front-b { top: 645px; }
  .card--back-b  { top: 935px; }

  /* Front: company name lockup */
  .brand { position: absolute; left: 94px; top: 104px; }
  .brand__name {
    display: flex;
    align-items: center;
    gap: 14px;
    font-weight: 300;
    font-size: 46px;
    line-height: 1;
    letter-spacing: 2px;
  }
  .brand__mark {
    width: 30px;
    height: 30px;
    border: 2px solid var(--ink);
  }
  .brand__line {
    margin-top: 8px;
    font-weight: 400;
    font-size: 22px;
    letter-spacing: 1.5px;
    line-height: 1;
  }
  .brand__tagline {
    margin-top: 6px;
    font-weight: 400;
    font-size: 12.5px;
    letter-spacing: 0.6px;
    line-height: 1;
  }

  /* Back: contact person */
  .person__mark {
    position: absolute;
    left: 86px;
    top: 92px;
    width: 30px;
    height: 30px;
    border: 2px solid var(--ink);
  }
  .person { position: absolute; left: 94px; top: 139px; }
  .person__name {
    font-weight: 300;
    font-size: 20px;
    line-height: 1.05;
    letter-spacing: 0.2px;
  }
  .person__name-lead { text-decoration: underline; text-decoration-thickness: 1.5px; text-underline-offset: -0.9em; }
  .person__role {
    font-weight: 300;
    font-size: 15px;
    letter-spacing: 1px;
    line-height: 1.1;
  }

  .contact {
    position: absolute;
    right: 8px;
    bottom: 10px;
    writing-mode: vertical-rl;
    transform: rotate(180deg);
    line-height: 1.15;
  }
  .contact__phone { font-size: 17px; font-weight: 400; letter-spacing: 0.8px; }
  .contact__email { font-size: 12.5px; font-weight: 400; }
</style>
</head>
<body>
<main class="canvas">

  <section class="card card--front-a" aria-label="Card front">
    <div class="brand">
      <div class="brand__name">BEXLEY <span class="brand__mark"></span></div>
      <div class="brand__line">BUILDS</div>
      <div class="brand__tagline">BUILDING AND CARPENTRY</div>
    </div>
  </section>

  <section class="card card--back-a" aria-label="Card back">
    <span class="person__mark"></span>
    <div class="person">
      <div class="person__name"><span class="person__name-lead">DORI</span>AN WEBB</div>
      <div class="person__role">project manager</div>
      <div class="person__role">carpenter</div>
    </div>
    <div class="contact">
      <div class="contact__phone">0471 839 204</div>
      <div class="contact__email">rbexleybuilds@maplorn.com</div>
    </div>
  </section>

  <section class="card card--front-b" aria-label="Card front">
    <div class="brand">
      <div class="brand__name">BEXLEY <span class="brand__mark"></span></div>
      <div class="brand__line">BUILDS</div>
      <div class="brand__tagline">BUILDING AND CARPENTRY</div>
    </div>
  </section>

  <section class="card card--back-b" aria-label="Card back">
    <span class="person__mark"></span>
    <div class="person">
      <div class="person__name"><span class="person__name-lead">DORI</span>AN WEBB</div>
      <div class="person__role">project manager</div>
      <div class="person__role">carpenter</div>
    </div>
    <div class="contact">
      <div class="contact__phone">0471 839 204</div>
      <div class="contact__email">rbexleybuilds@maplorn.com</div>
    </div>
  </section>

</main>
</body>
</html>
```